Wellness, Meaning, and the Inner Journey Research Program Website

Overview: This website will serve a new research program (Wellness, Meaning, and the Inner Journey) at the Harrowgate University School of Medicine. I want a clean, intuitive design that has a navigation bar, but uses icons/graphic buttons to link to the main pages. In an attached Word document, I have provided a basic information architecture for the site, understanding that this project would just generate graphics and code for the 3 pages. I highlighted the 3 pages I'd like designed.
Target market: People who want to participate in our research, or contribute grant funding to specific projects.
Number of page: The design project focuses on 3 pages, but the site must accommodate 6 pages with top-level links. See attached Word doc.
Logo and website header: Please integrate our logo in the header. I've uploaded it as a png file--both with the name of the website and with just the logo image. I imaging the logo would look great in a banner set against an image of a mountain. The two main design themes I want to see included are nature and healthcare.
Text content: I have not yet provided text. Use some dummy text.
Technical Specifications:
- Build using WordPress. We will host this site ourselves on NetHarbor using WordPress.
- The design package must be coded.
- The template must be responsive to different platforms (e.g., computer, mobile phone, iPad).
Thank you! I look forward to seeing your designs.
- Ned

```html
<!DOCTYPE html>
<html lang="en">
<head>
<meta charset="utf-8">
<title>Wellness, Meaning, and the Inner Journey – The Research Program</title>
<link rel="stylesheet" href="https://fonts.googleapis.com/css2?family=Baloo+2:wght@600;700;800&family=Poppins:wght@400;500;600&display=swap">
<style>
:root{
  --blue:#1d5f97;
  --green:#4c9d35;
  --green-soft:#5aa83c;
  --teal:#14a27e;
  --teal-dark:#0e8f6d;
  --ink:#222;
  --muted:#555;
  --tint:#f1f6ef;
  --field:#f3f5f3;
  --btn:linear-gradient(90deg,#1f5c98,#4c9d35);
}
*{margin:0;padding:0;box-sizing:border-box}
html,body{width:1200px;height:3712px;overflow:hidden}
body{font-family:"Poppins",sans-serif;color:var(--ink);background:#fff;position:relative}
section,header,footer{position:absolute;left:0;width:1200px}
.abs{position:absolute}
.center{left:0;width:1200px;text-align:center}
.btn{position:absolute;display:flex;align-items:center;justify-content:center;color:#fff;font-size:13px;background:var(--btn);border-radius:3px;box-shadow:0 2px 4px rgba(0,0,0,.15)}
.sec-title{position:absolute;left:0;width:1200px;text-align:center;font-family:"Baloo 2",sans-serif;font-weight:800;font-size:40px;line-height:1;color:var(--blue)}
.sec-title span{color:var(--green)}
.divider{position:absolute;left:540px;width:120px;height:8px}
.lead{position:absolute;left:0;width:1200px;text-align:center;font-size:14px;line-height:23px;color:#333}

/* header / hero */
.hero{top:0;height:598px;background:linear-gradient(180deg,#97acd9 0%,#b6c5e6 30%,#d6deef 55%,#c3cce2 72%,#7f93bd 100%)}
.nav{position:absolute;top:0;left:0;width:1200px;height:58px;background:rgba(160,178,220,.75);border-bottom:1px solid rgba(255,255,255,.4)}
.nav-item{position:absolute;top:11px;width:100px;margin-left:-50px;text-align:center;color:#fff;font-size:13px}
.nav-item svg{display:block;margin:0 auto 4px}
.nav-item.active{color:var(--blue)}
.nav-item.active::after{content:"";display:block;width:40px;height:2px;background:var(--blue);margin:3px auto 0}
.brand-mark{position:absolute;left:555px;top:105px;width:90px;height:90px;border-radius:50%;background:linear-gradient(135deg,#2a6aa6,#4c9d35)}
.hero-title{top:218px;font-family:"Baloo 2",sans-serif;font-weight:800;font-size:40px;color:var(--blue);line-height:1}
.hero-sub{top:260px;font-family:"Baloo 2",sans-serif;font-weight:800;font-size:31px;color:var(--green);line-height:1}
.hero-text{top:304px;font-size:23px;line-height:36px;color:#111}

/* vision */
.vision{top:598px;height:799px;background:var(--tint)}
.card{position:absolute;top:269px;width:274px;height:375px;background:#fff;border-radius:10px;box-shadow:0 0 10px rgba(0,0,0,.12);text-align:center}
.card-photo{position:absolute;left:9px;top:7px;width:256px;height:182px;border-radius:6px 6px 0 0}
.card-icon{position:absolute;left:99px;top:148px;width:76px;height:76px;border-radius:50%;background:linear-gradient(135deg,#1f5c98,#4c9d35);border:4px solid #fff;display:flex;align-items:center;justify-content:center}
.card h3{position:absolute;top:243px;left:0;width:100%;font-size:15px;font-weight:500}
.card p{position:absolute;top:270px;left:20px;right:20px;font-size:13.5px;line-height:23px;color:#333}

/* pillars */
.pillars{top:1397px;height:774px;background:#fff}
.pillar h3{position:absolute;font-size:20px;font-weight:400;color:#222}
.pillar p{position:absolute;font-size:11.5px;line-height:19px;color:#666}
.pillar a{position:absolute;font-size:15px;color:var(--green);text-decoration:none;font-weight:500}

/* projects */
.projects{top:2171px;height:583px;background:var(--tint)}
.proj{position:absolute;top:202px;width:199px;height:260px;border-radius:6px;color:#fff;text-align:center}
.proj h4{position:absolute;left:0;width:100%;font-size:15px;font-weight:600}
.proj p{position:absolute;left:0;width:100%;font-size:12px}
.plus{position:absolute;left:83px;width:32px;height:32px;border-radius:50%;background:#fff;display:flex;align-items:center;justify-content:center}
.arrow{position:absolute;top:2484px;width:36px;height:36px;border:1.5px solid #1d5f97;border-radius:50%;display:flex;align-items:center;justify-content:center;background:#fff}

/* form */
.contact{top:2754px;height:592px;background:#fff}
.field{position:absolute;height:44px;background:var(--field);display:flex;align-items:center;font-size:12px;color:#333}
.field .ico{width:40px;height:100%;display:flex;align-items:center;justify-content:center;border-right:1px solid #e2e5e2;margin-right:14px}
.field.area{align-items:flex-start}
.field.area .ico{height:40px;border-right:1px solid #e2e5e2}
.field.area .label{padding-top:24px}

/* footer */
.site-footer{top:3346px;height:366px;background:var(--teal);color:#fff}
.foot-brand{position:absolute;left:161px;top:85px;display:flex;align-items:center;gap:10px}
.foot-brand i{width:46px;height:46px;border-radius:50%;background:#fff;opacity:.9;display:block}
.foot-brand b{font-size:12px;font-weight:600;line-height:14px}
.foot-text{position:absolute;left:161px;top:153px;width:310px;font-size:11.5px;line-height:19.5px}
.social{position:absolute;top:240px;width:22px;height:22px;border-radius:50%;background:#fff}
.foot-h{position:absolute;top:88px;font-size:18px;font-weight:500;letter-spacing:.3px;border-bottom:1px solid rgba(255,255,255,.6);padding-bottom:2px}
.foot-link{position:absolute;font-size:12.5px}
.contact-row{position:absolute;left:815px;display:flex;gap:13px;font-size:12.5px;line-height:20px}
.copyright{position:absolute;left:0;top:313px;width:1200px;height:53px;background:var(--teal-dark);text-align:center;font-size:12.5px;line-height:53px}
</style>
</head>
<body>

<header class="hero">
  <div class="abs" role="img" aria-label="Photograph of a snow-capped mountain peak under a blue sky" style="inset:0"></div>
  <nav class="nav">
    <div class="nav-item active" style="left:264px">
      <svg width="18" height="16" viewBox="0 0 18 16" fill="none" stroke="currentColor" stroke-width="1.5"><path d="M2 7 9 1l7 6M4 6v9h10V6"/></svg>Home</div>
    <div class="nav-item" style="left:389px">
      <svg width="20" height="16" viewBox="0 0 20 16" fill="none" stroke="currentColor" stroke-width="1.4"><circle cx="7" cy="5" r="3"/><circle cx="14" cy="5" r="2.5"/><path d="M1 15c0-4 3-6 6-6s6 2 6 6M13 9c3 0 6 2 6 5"/></svg>People</div>
    <div class="nav-item" style="left:514px">
      <svg width="18" height="16" viewBox="0 0 18 16" fill="none" stroke="currentColor" stroke-width="1.4"><rect x="2" y="3" width="11" height="12"/><path d="M7 10l9-9"/></svg>Projects</div>
    <div class="nav-item" style="left:640px">
      <svg width="18" height="16" viewBox="0 0 18 16" fill="none" stroke="currentColor" stroke-width="1.4"><circle cx="9" cy="8" r="7"/><path d="M7 6a2 2 0 1 1 2 2v2M9 12v1"/></svg>Resources</div>
    <div class="nav-item" style="left:765px">
      <svg width="18" height="16" viewBox="0 0 18 16" fill="none" stroke="currentColor" stroke-width="1.4"><circle cx="9" cy="8" r="6.5"/><circle cx="9" cy="8" r="3"/></svg>Faq's</div>
    <div class="nav-item" style="left:890px">
      <svg width="18" height="16" viewBox="0 0 18 16" fill="none" stroke="currentColor" stroke-width="1.4"><path d="M4 2h4l1 4-2 1c1 2 2 3 4 4l1-2 4 1v4c-8 0-12-5-12-12z"/></svg>Contact Us</div>
  </nav>
  <div class="brand-mark"></div>
  <h1 class="abs center hero-title">Wellness, Meaning, and the Inner Journey</h1>
  <div class="abs center hero-sub">The Research Program</div>
  <p class="abs center hero-text">Lorem Ipsum Dolor Sit Amet, Consectetur Adipiscing Elit,<br>Sed Do Eiusmod Tempor Incididunt Ut Labore</p>
  <a class="btn" style="left:524px;top:428px;width:141px;height:39px">Contact Us</a>
</header>

<section class="vision">
  <h2 class="sec-title" style="top:70px">Our <span>Vision</span></h2>
  <svg class="divider" style="top:110px" viewBox="0 0 120 8"><path d="M15 4h38M67 4h38" stroke="#bcd5b4"/><circle cx="60" cy="4" r="3" fill="#4c9d35"/></svg>
  <p class="lead" style="top:138px">Lorem ipsum dolor sit amet, consectetur adipiscing elit, sed do eiusmod tempor incididunt ut labore et dolore magna<br>aliqua. Ut enim ad minim veniam,  quis nostrud exercitation ullamco laboris. Lorem ipsum dolor sit amet, magna aliqua.<br>Ut enim ad minim veniam,  quis nostrud exercitation ullamco laboris</p>

  <div class="card" style="left:160px">
    <div class="card-photo" role="img" aria-label="Photo of colleagues working together at a laptop" style="background:linear-gradient(135deg,#cdbba4,#8a7057)"></div>
    <div class="card-icon"><svg width="40" height="32" viewBox="0 0 40 32" fill="none" stroke="#fff" stroke-width="1.8"><circle cx="20" cy="9" r="5"/><circle cx="8" cy="12" r="3.5"/><circle cx="32" cy="12" r="3.5"/><path d="M11 30c0-6 4-10 9-10s9 4 9 10zM2 28c0-5 3-8 6-8M38 28c0-5-3-8-6-8"/></svg></div>
    <h3>PEOPLE</h3>
    <p>Lorem Ipsum Dolor Sit Amet, Consectetur Adipiscing Elit, Sed Do Labore Et Dolore Magna</p>
  </div>
  <div class="card" style="left:464px">
    <div class="card-photo" role="img" aria-label="Photo of researchers working in a laboratory" style="background:linear-gradient(135deg,#e6e9ee,#a9b3bd)"></div>
    <div class="card-icon"><svg width="32" height="36" viewBox="0 0 32 36" fill="none" stroke="#fff" stroke-width="1.8"><rect x="3" y="5" width="22" height="28" rx="2"/><rect x="9" y="2" width="10" height="5" rx="1"/><path d="M7 14h8M7 20h8M7 26h8"/><circle cx="25" cy="12" r="5"/><path d="M23 12l2 2 3-3"/></svg></div>
    <h3>PROJECTS</h3>
    <p>Lorem Ipsum Dolor Sit Amet, Consectetur Adipiscing Elit, Sed Do Labore Et Dolore Magna</p>
  </div>
  <div class="card" style="left:765px">
    <div class="card-photo" role="img" aria-label="Photo of a thoughtful man before a chalkboard of question marks" style="background:linear-gradient(135deg,#4a4a4a,#262626)"></div>
    <div class="card-icon"><svg width="38" height="34" viewBox="0 0 38 34" fill="none" stroke="#fff" stroke-width="1.8"><rect x="2" y="12" width="22" height="14" rx="3"/><path d="M7 26v6l6-6"/><circle cx="27" cy="10" r="8"/><path d="M25 8a2 2 0 1 1 2 2v2M27 14v1"/></svg></div>
    <h3 style="top:245px">FAQ'S</h3>
    <p>Lorem Ipsum Dolor Sit Amet, Consectetur Adipiscing Elit, Sed Do Labore Et Dolore Magna</p>
  </div>

  <a class="btn" style="left:530px;top:681px;width:140px;height:39px">Read More</a>
</section>

<section class="pillars">
  <h2 class="sec-title" style="top:72px">Our <span>Three Pillars</span></h2>
  <svg class="divider" style="top:112px" viewBox="0 0 120 8"><path d="M15 4h38M67 4h38" stroke="#bcd5b4"/><circle cx="60" cy="4" r="3" fill="#4c9d35"/></svg>
  <p class="lead" style="top:147px">Lorem Ipsum Dolor Sit Amet, Consectetur Adipiscing Elit, Sed Do Eiusmod<br>Tempor Incididunt Ut Labore Et Dolore.</p>

  <svg class="abs" style="left:0;top:0" width="1200" height="774" viewBox="0 0 1200 774">
    <path d="M428 329 A167 164 0 0 0 761 329" fill="none" stroke="#7fb26b" stroke-width="1.2" stroke-dasharray="5 4"/>
    <circle cx="428" cy="329" r="5" fill="#4c9d35"/>
    <circle cx="761" cy="329" r="5" fill="#4c9d35"/>
    <circle cx="596" cy="493" r="5" fill="#4c9d35"/>
    <circle cx="597" cy="346" r="110" fill="none"/>
    <!-- health care icon -->
    <g fill="none" stroke="#1d5f97" stroke-width="1.6" transform="translate(358,306)">
      <path d="M20 40 4 24C-3 16 3 2 13 4c4 1 6 4 7 6 1-2 3-5 7-6 10-2 16 12 9 20L20 40z"/>
      <path d="M3 22h9l3-7 4 12 3-5h6" stroke="#4c9d35"/>
      <circle cx="46" cy="22" r="7" stroke="#4c9d35"/><path d="M46 18v8M42 22h8" stroke="#4c9d35"/>
    </g>
    <!-- values icon -->
    <g fill="none" stroke="#1d5f97" stroke-width="1.6" transform="translate(777,300)">
      <path d="M2 16h32L18 40z"/><path d="M8 8h20l6 8M8 8l-6 8M12 16l6 24 6-24M12 16l6-8 6 8"/>
      <circle cx="36" cy="8" r="7" stroke="#4c9d35"/><circle cx="36" cy="8" r="3" stroke="#4c9d35"/>
    </g>
    <!-- spiritual icon -->
    <g fill="none" stroke="#1d5f97" stroke-width="1.6" transform="translate(574,508)">
      <path d="M22 2 42 40H2z"/><path d="M8 28c8-10 20-10 28 0-8 10-20 10-28 0z" stroke="#4c9d35"/><circle cx="22" cy="28" r="4"/>
    </g>
  </svg>
  <div class="abs" role="img" aria-label="Large program emblem" style="left:492px;top:243px;width:210px;height:210px;border-radius:50%;background:radial-gradient(circle,#3a87a0 0%,#4c9d35 70%);opacity:.9"></div>

  <div class="pillar">
    <h3 style="left:113px;width:300px;text-align:right;top:366px">Health care</h3>
    <p style="left:113px;width:300px;text-align:right;top:398px">Lorem Ipsum Dolor Sit Amet, Consectetur<br>Adipiscing Elit, Sed Do Eiusmod Tempor<br>Incididunt Ut Labore Et Dolore Magna</p>
    <a style="left:113px;width:300px;text-align:right;top:456px">Know More</a>
  </div>
  <div class="pillar">
    <h3 style="left:782px;top:366px">Values</h3>
    <p style="left:782px;top:398px">Lorem Ipsum Dolor Sit Amet, Consectetur<br>Adipiscing Elit, Sed Do Eiusmod Tempor<br>Incididunt Ut Labore Et Dolore Magna</p>
    <a style="left:782px;top:458px">Know More</a>
  </div>
  <div class="pillar">
    <h3 style="left:0;width:1200px;text-align:center;top:570px">Spiritual Life</h3>
    <p style="left:0;width:1200px;text-align:center;top:602px">Lorem Ipsum Dolor Sit Amet, Consectetur<br>Adipiscing Elit, Sed Do Eiusmod Tempor Incididunt<br>Ut Labore Et Dolore Magna</p>
    <a style="left:0;width:1186px;text-align:center;top:662px">Know More</a>
  </div>
</section>

<section class="projects">
  <h2 class="sec-title" style="top:72px">Our <span>Projects</span></h2>
  <svg class="divider" style="top:112px" viewBox="0 0 120 8"><path d="M15 4h38M67 4h38" stroke="#bcd5b4"/><circle cx="60" cy="4" r="3" fill="#4c9d35"/></svg>
  <p class="lead" style="top:140px">Lorem Ipsum Dolor Sit Amet, Consectetur Adipiscing Elit, Sed Do</p>

  <div class="proj" role="img" aria-label="Photo of scientists examining a sample in a lab" style="left:160px;background:linear-gradient(180deg,#2f6bb0,#1c3f6e)">
    <h4 style="top:196px">Project 1</h4><p style="top:221px">Lorem Ipsum Dolor Sit Amet</p>
    <div class="plus" style="top:244px"><svg width="12" height="12"><path d="M6 1v10M1 6h10" stroke="#111" stroke-width="2.4"/></svg></div>
  </div>
  <div class="proj" role="img" aria-label="Photo of a laboratory researcher under a green highlight" style="left:387px;background:#5aa83c;border:4px solid #e0b88f">
    <h4 style="top:129px">Project 2</h4><p style="top:152px">Lorem Ipsum Dolor Sit Amet</p>
    <div class="plus" style="top:181px;left:79px"><svg width="12" height="12"><path d="M6 1v10M1 6h10" stroke="#111" stroke-width="2.4"/></svg></div>
  </div>
  <div class="proj" role="img" aria-label="Photo of two businessmen talking" style="left:612px;background:linear-gradient(180deg,#4a4a4a,#202020)">
    <h4 style="top:196px">Project 3</h4><p style="top:221px">Lorem Ipsum Dolor Sit Amet</p>
    <div class="plus" style="top:244px"><svg width="12" height="12"><path d="M6 1v10M1 6h10" stroke="#111" stroke-width="2.4"/></svg></div>
  </div>
  <div class="proj" role="img" aria-label="Photo of colleagues smiling in an office" style="left:838px;background:linear-gradient(180deg,#a2a6ab,#4e525a)">
    <h4 style="top:196px">Project 4</h4><p style="top:221px">Lorem Ipsum Dolor Sit Amet</p>
    <div class="plus" style="top:244px"><svg width="12" height="12"><path d="M6 1v10M1 6h10" stroke="#111" stroke-width="2.4"/></svg></div>
  </div>
</section>
<div class="arrow" style="left:84px"><svg width="10" height="12"><path d="M7 1 2 6l5 5" fill="none" stroke="#1d5f97" stroke-width="1.8"/></svg></div>
<div class="arrow" style="left:1075px"><svg width="10" height="12"><path d="M3 1l5 5-5 5" fill="none" stroke="#1d5f97" stroke-width="1.8"/></svg></div>

<section class="contact">
  <h2 class="sec-title" style="top:70px">Our <span>Projects</span></h2>
  <svg class="divider" style="top:110px" viewBox="0 0 120 8"><path d="M15 4h38M67 4h38" stroke="#bcd5b4"/><circle cx="60" cy="4" r="3" fill="#4c9d35"/></svg>
  <p class="lead" style="top:135px">Lorem Ipsum Dolor Sit Amet, Consectetur Adipiscing Elit, Sed Do</p>

  <div class="field" style="left:239px;top:196px;width:343px"><span class="ico"><svg width="12" height="12" fill="#aaa"><circle cx="6" cy="3.5" r="3"/><path d="M0 12c0-4 3-5 6-5s6 1 6 5z"/></svg></span>Your Name*</div>
  <div class="field" style="left:609px;top:196px;width:343px"><span class="ico"><svg width="10" height="13" fill="#aaa"><path d="M5 0a5 5 0 0 1 5 5c0 3-5 8-5 8S0 8 0 5a5 5 0 0 1 5-5z"/><circle cx="5" cy="5" r="2" fill="#f3f5f3"/></svg></span>Email*</div>
  <div class="field" style="left:239px;top:254px;width:343px"><span class="ico"><svg width="12" height="12" fill="#aaa"><path d="M1 1h3l1 3-2 1c1 2 2 3 4 4l1-2 3 1v3C5 11 1 7 1 1z"/></svg></span>Phone*</div>
  <div class="field" style="left:609px;top:254px;width:343px"><span class="ico"><svg width="14" height="12" fill="none" stroke="#aaa" stroke-width="1.3"><rect x="1" y="2" width="9" height="9"/><path d="M6 7l7-6"/></svg></span>Inquiry For*</div>
  <div class="field area" style="left:239px;top:317px;width:712px;height:108px"><span class="ico"><svg width="14" height="14" fill="none" stroke="#aaa" stroke-width="1.2"><circle cx="7" cy="7" r="6"/><path d="M5.5 5.5a1.5 1.5 0 1 1 1.5 1.5v1.5M7 10v.5"/></svg></span><span class="label">How can we help you?</span></div>

  <a class="btn" style="left:530px;top:474px;width:140px;height:39px">Submit Now</a>
</section>

<footer class="site-footer">
  <div class="foot-brand"><i></i><b>Wellness, Meaning, and the Inner Journey<br>The Research Program</b></div>
  <p class="foot-text">Lorem Ipsum Dolor Sit Amet, Consectetur Adipiscing Elit, Sed Do Eiusmod Tempor Incididunt Ut Labore Et Dolore Magna</p>
  <span class="social" style="left:161px"></span>
  <span class="social" style="left:198px"></span>
  <span class="social" style="left:236px"></span>
  <span class="social" style="left:274px"></span>

  <h4 class="foot-h" style="left:547px">QUICK LINKS</h4>
  <span class="foot-link" style="left:548px;top:130px">Home</span>
  <span class="foot-link" style="left:651px;top:130px">Resources</span>
  <span class="foot-link" style="left:548px;top:166px">Our Vision</span>
  <span class="foot-link" style="left:651px;top:166px">Faq's</span>
  <span class="foot-link" style="left:548px;top:203px">People</span>
  <span class="foot-link" style="left:651px;top:205px">Contact Us</span>
  <span class="foot-link" style="left:548px;top:244px">Projects</span>

  <h4 class="foot-h" style="left:810px">CONTACT DETAILS</h4>
  <div class="contact-row" style="top:128px"><svg width="10" height="14" fill="#fff"><path d="M5 0a5 5 0 0 1 5 5c0 3-5 9-5 9S0 8 0 5a5 5 0 0 1 5-5z"/><circle cx="5" cy="5" r="2" fill="#14a27e"/></svg><span>12, Society Name, Street,<br>City, State</span></div>
  <div class="contact-row" style="top:190px"><svg width="12" height="14" fill="#fff"><path d="M1 2h3l1 3-2 1c1 2 2 3 4 4l1-2 3 1v3C5 12 1 8 1 2z"/></svg><span>123-456-7890</span></div>
  <div class="contact-row" style="top:243px"><svg width="13" height="14" fill="none" stroke="#fff" stroke-width="1.3"><rect x="1" y="3" width="11" height="8"/><path d="M1 3l5.5 4L12 3"/></svg><span>info@wmijresearch.org</span></div>

  <div class="copyright">Copyright © 2021 WMIJ Research Program. All Rights Reserved.</div>
</footer>

</body>
</html>
```